Zvo Klinieken website for a maxillofacial surgery clinic

It's a website for a clinic for maxillofacial surgery in WordPress . The website doesn't need to be complicated but has to look professional. It needs to be in Dutch so i can give the texts. Similar websites are www.tandartsenpraktijkveldorm.nl or www.pbtspecialisten.nl. Pages would be sort of similar to https://hetcentrumvoorgezichtszorg.nl/ or https://wervelmondclinics.nl/. Those lasts are maxillofacial surgery clinic websites, but there are little more extensive.
I uploaded the logo. If this is not the proper quality i can upload the eps. Logo was made through pixelforum.

Target Market(s)

Patients who can find me and see information about the clinic

Industry/Entity Type

Healthcare

Coding

Coded - Design and coding required

Number of Pages Required

5+ page

Font styles to use
Other font styles liked:
• Something standard professional

Colors
0054AA
0677BA
7BADD7
CADEEF
E8F1F8

Requirements
Nice to have
• Something in line with the logo. I prefer a little dark like the darker logos but I'm not sure if that's professional. Logos bkvzo and rlpw are instances i'm registered to so they will have to be on the website too but small somewhere.

```html
<!DOCTYPE html>
<html lang="nl">
<head>
<meta charset="utf-8">
<title>Zvo Klinieken</title>
<link href="https://fonts.googleapis.com/css2?family=Roboto:wght@300;400;500;700;900&display=swap" rel="stylesheet">
<style>
:root{
  --blue:#1fa0e3;
  --blue-deep:#0677BA;
  --blue-light:#7BADD7;
  --sky:#CADEEF;
  --mist:#E8F1F8;
  --ink:#111;
  --text:#555;
  --white:#fff;
  --black:#000;
}
*{box-sizing:border-box;margin:0;padding:0}
html,body{width:1200px;height:3945px;overflow:hidden;background:var(--white)}
body{font-family:'Roboto',Arial,sans-serif;color:var(--ink)}
.page{position:relative;width:1200px;height:3945px;overflow:hidden}
.abs{position:absolute}

/* header */
.topbar{position:absolute;left:530px;top:0;width:670px;height:38px;background:#f1f1f1;clip-path:polygon(25px 0,100% 0,100% 100%,0 100%)}
.topbar-item{position:absolute;top:9px;font-size:14px;color:#333;display:flex;align-items:center;gap:14px;white-space:nowrap}
.ico-circle{width:26px;height:26px;border-radius:50%;background:var(--blue);display:flex;align-items:center;justify-content:center}
.brand{position:absolute;left:112px;top:30px;display:flex;align-items:center;gap:10px;font-size:28px;font-weight:500;color:var(--blue-deep);white-space:nowrap}
.brand-dot{width:14px;height:14px;border-radius:50%;background:var(--blue);flex:none}
.nav{position:absolute;top:66px;left:438px;display:flex;font-size:15px;font-weight:500;white-space:nowrap}
.nav a{color:#222;text-decoration:none;margin-right:24px}
.nav a.active{color:var(--blue)}
.btn{display:inline-flex;align-items:center;justify-content:center;gap:10px;background:var(--blue);color:var(--white);font-weight:500;font-size:15px;text-decoration:none;white-space:nowrap}
.appt{position:absolute;left:877px;top:56px;width:211px;height:39px}

/* hero */
.hero{position:absolute;left:0;top:109px;width:1200px;height:700px;background:linear-gradient(90deg,#fafafa 0%,#f0f2f4 45%,#e8ecef 100%)}
.hero-photo{position:absolute;left:520px;top:0;width:680px;height:640px;background:linear-gradient(135deg,#dfe6ec 0%,#c9d6e2 40%,#e9eef2 100%)}
.welcome{position:absolute;left:112px;top:188px;font-size:19px;font-weight:500}
.hero-title{position:absolute;left:112px;top:222px;font-size:70px;font-weight:700;letter-spacing:1px;color:var(--ink);white-space:nowrap;line-height:80px}
.hero-text{position:absolute;left:112px;top:303px;width:400px;font-size:14px;line-height:24px;color:#222}
.callback{position:absolute;left:112px;top:368px;width:469px;height:62px;border:1.5px solid var(--blue);background:var(--white);padding:10px}
.callback .field{position:absolute;left:12px;top:10px;width:286px;height:40px;background:#f1f1f1;font-size:13px;color:#777;padding:12px 10px}
.callback .btn{position:absolute;left:313px;top:10px;width:143px;height:40px}
.doctor-tag{position:absolute;left:763px;top:275px;width:184px;height:48px;background:var(--white);border-radius:24px 4px 4px 24px;box-shadow:0 2px 6px rgba(0,0,0,.08)}
.doctor-tag .av{position:absolute;left:4px;top:4px;width:40px;height:40px;border-radius:50%;background:#cfd8df}
.doctor-tag b{position:absolute;left:56px;top:8px;font-size:14px;font-weight:500}
.doctor-tag span{position:absolute;left:56px;top:27px;font-size:11px;color:#666}

/* about */
.eyebrow{font-size:19px;color:var(--blue)}
.section-title{font-size:40px;font-weight:700}
.about-label{left:641px;top:776px}
.about-rule{left:641px;top:806px;width:28px;height:2px;background:var(--ink)}
.about-title{left:639px;top:820px}
.about-text{left:641px;top:900px;width:450px;font-size:14px;line-height:23px;color:#555}
.about-text p{margin-bottom:23px}
.checks{left:641px;top:1126px;list-style:none;font-size:14px;color:#222}
.checks li{display:flex;align-items:center;gap:19px;height:37px;white-space:nowrap}
.chk{width:22px;height:22px;border-radius:50%;border:1px solid #999;display:flex;align-items:center;justify-content:center}
.chk.on{background:var(--blue);border-color:var(--blue)}
.about-btn{left:641px;top:1266px;width:211px;height:40px}
.about-frame{left:112px;top:871px;width:446px;height:383px;border:1.5px solid var(--blue)}
.about-photo{left:114px;top:873px;width:442px;height:379px;background:linear-gradient(180deg,#eef2f5 0%,#cfdbe6 55%,#4a7fb5 100%)}
.logo-board{left:201px;top:1111px;width:279px;height:210px;background:linear-gradient(160deg,#3b4048,#22262c);display:flex;align-items:center;justify-content:center;gap:12px;font-size:30px;font-weight:500;color:var(--sky);white-space:nowrap}

/* services */
.services{left:0;top:1407px;width:1200px;height:254px;background:var(--blue)}
.services-photo{left:0;top:1661px;width:1200px;height:586px;background:linear-gradient(120deg,#4c6fb6 0%,#8aa3c9 40%,#d9d2cc 70%,#eeeeee 100%)}
.center-head{left:0;width:1200px;text-align:center}
.rule-c{left:589px;width:22px;height:2px}
.cards{left:112px;top:1592px;display:flex;gap:13px}
.card{width:152px;height:143px;background:var(--white);border-radius:6px;box-shadow:0 3px 8px rgba(0,0,0,.12);display:flex;flex-direction:column;align-items:center;padding-top:18px;text-align:center;font-size:14px;font-weight:500;color:#222}
.card svg{margin-bottom:10px}
.card.sel{border-bottom:2px solid var(--blue)}
.arrow-btn{width:40px;height:40px;border-radius:50%;background:var(--white);display:flex;align-items:center;justify-content:center;top:1945px}
.services-btn{left:495px;top:2248px;width:211px;height:39px}

/* team */
.team{left:0;top:2372px;width:1200px;height:545px;background:linear-gradient(90deg,#1da0e6 0%,#4fbdf1 60%,#86d3f8 100%)}
.expert{top:2596px;width:198px;height:232px;border:1px solid var(--white);background:linear-gradient(180deg,#f3f3f3 0%,#e3d7dd 50%,#8e4f86 100%)}
.expert.hover{background:linear-gradient(180deg,#cfe6f3 0%,#7fb8dd 100%)}
.expert .cap{position:absolute;bottom:40px;width:100%;text-align:center;color:var(--white);font-size:15px}
.fb{width:50px;height:50px;border-radius:50%;background:var(--white);top:2803px;display:flex;align-items:center;justify-content:center;box-shadow:0 2px 6px rgba(0,0,0,.1);color:var(--blue);font-size:16px;font-weight:700}

/* testimonials */
.quote-card{top:3137px;width:297px;height:261px;padding:18px 24px}
.quote-card.lift{background:var(--white);box-shadow:0 2px 12px rgba(0,0,0,.15)}
.qmark{font-size:28px;font-weight:900;color:#555;line-height:24px;height:24px}
.quote-card p{margin-top:18px;font-size:14px;line-height:23px;color:#666}
.who{display:flex;align-items:center;gap:14px;margin-top:13px}
.who .av{width:52px;height:52px;border-radius:50%;background:#c9cfd4}
.who b{display:block;font-size:13px;font-weight:500}
.who span{font-size:12px;color:#666}
.dots{left:579px;top:3443px;display:flex;gap:5px}
.dots i{width:7px;height:7px;border-radius:50%;background:var(--blue)}
.dots i.off{background:var(--blue-light)}

/* footer */
.footer-bg{left:0;top:3600px;width:1200px;height:345px;background:var(--black)}
.footer-mark{left:800px;top:3600px;font-size:50px;line-height:60px;font-weight:500;color:#14202a;white-space:nowrap}
.foot-brand{left:112px;top:3735px;font-size:30px;font-weight:500;color:var(--white);display:flex;align-items:center;gap:10px}
.socials{left:133px;top:3820px;display:flex;gap:11px}
.socials i{width:28px;height:28px;border-radius:50%;background:var(--white)}
.fcol{top:3704px;color:var(--white);font-size:14px;line-height:23px}
.fcol h4{font-weight:400;text-decoration:underline;font-size:14px;margin-bottom:12px}
.copy{left:0;top:3893px;width:1200px;text-align:center;color:var(--white);font-size:14px}
</style>
</head>
<body>
<div class="page">

  <header>
    <div class="topbar">
      <div class="topbar-item" style="left:70px"><span class="ico-circle"><svg width="12" height="12" viewBox="0 0 24 24"><path fill="#fff" d="M6.6 10.8a15 15 0 0 0 6.6 6.6l2.2-2.2c.3-.3.7-.4 1-.2 1.1.4 2.3.6 3.6.6.6 0 1 .4 1 1V20c0 .6-.4 1-1 1A17 17 0 0 1 3 4c0-.6.4-1 1-1h3.5c.6 0 1 .4 1 1 0 1.3.2 2.5.6 3.6.1.3 0 .7-.2 1z"/></svg></span>+31 (20) 555 0187</div>
      <div class="topbar-item" style="left:300px"><span class="ico-circle"><svg width="12" height="12" viewBox="0 0 24 24"><path fill="#fff" d="M6.6 10.8a15 15 0 0 0 6.6 6.6l2.2-2.2c.3-.3.7-.4 1-.2 1.1.4 2.3.6 3.6.6.6 0 1 .4 1 1V20c0 .6-.4 1-1 1A17 17 0 0 1 3 4c0-.6.4-1 1-1h3.5c.6 0 1 .4 1 1 0 1.3.2 2.5.6 3.6.1.3 0 .7-.2 1z"/></svg></span>info@zvoklinieken.nl</div>
      <div class="topbar-item" style="left:516px;top:12px;gap:12px">
        <svg width="13" height="13" viewBox="0 0 24 24"><circle cx="10" cy="10" r="6.5" fill="none" stroke="#222" stroke-width="3"/><path d="M15 15l6 6" stroke="#222" stroke-width="3"/></svg>
        <svg width="12" height="13" viewBox="0 0 24 24"><circle cx="12" cy="7" r="5.5" fill="#222"/><path d="M2 24c0-6 4.5-10 10-10s10 4 10 10z" fill="#222"/></svg>
      </div>
    </div>
    <div class="brand"><span class="brand-dot"></span>Zvo Klinieken</div>
    <nav class="nav"><a class="active" href="#">Home</a><a href="#">Treatments</a><a href="#">Practice</a><a href="#">Contact</a><a href="#">Absence</a></nav>
    <a class="btn appt" href="#">Make An Appointment</a>
  </header>

  <section class="hero">
    <div class="hero-photo" role="img" aria-label="Photo of a smiling surgeon and a dental assistant with a tablet in a treatment room"></div>
    <div class="doctor-tag"><span class="av" role="img" aria-label="Small portrait of the dentist"></span><b>Veldkamp</b><span>Best Dental Doctor</span></div>
    <p class="welcome">Welcome To</p>
    <h1 class="hero-title">Zvo Klinieken</h1>
    <p class="hero-text">Lorem ipsum dolor sit amet, consectetur adipiscing elit, sed do eiusmod tempor incididunt</p>
    <form class="callback"><span class="field">Enter Email Address</span><a class="btn" href="#">Get Call Back</a></form>
    <svg class="abs" style="left:0;top:480px" width="1200" height="220" viewBox="0 0 1200 220">
      <path d="M0 220 L0 80 L118 212 C420 112 760 42 1200 38 L1200 220 Z" fill="#fff"/>
      <path d="M5 74 L118 206 C420 106 760 36 1200 32 L1200 0 C1120 -2 1020 8 900 26 C640 62 380 132 118 182 Z" fill="#1fa0e3"/>
      <path d="M900 26 C1020 8 1120 -2 1200 0 L1200 18 C1110 12 1010 18 900 34 Z" fill="#9fd6f3"/>
    </svg>
  </section>

  <section>
    <p class="abs eyebrow about-label">About Us</p>
    <span class="abs about-rule"></span>
    <h2 class="abs section-title about-title">ZVO KLINIEKEN</h2>
    <div class="abs about-text">
      <p>The oral surgeon specializes in oral diseases, jaw and facial surgery (ZVO) and is therefore also called an ZVO surgeon. The oral surgeon has extensive experience in treating conditions of the mouth, jaw and face.</p>
      <p>These conditions can be congenital. This is, for example, the case with a cleft lip. But the conditions can also have developed later, for example as a result of an accident or illness. For example, you may have experienced a traffic accident in which you suffered serious</p>
    </div>
    <ul class="abs checks">
      <li><span class="chk on"><svg width="8" height="8" viewBox="0 0 10 10"><path d="M3 1l4 4-4 4" stroke="#fff" stroke-width="2" fill="none"/></svg></span>Lorem ipsum dolor sit amet, consectetur adipiscing Loremipsl</li>
      <li><span class="chk"><svg width="8" height="8" viewBox="0 0 10 10"><path d="M3 1l4 4-4 4" stroke="#333" stroke-width="1.5" fill="none"/></svg></span>Lorem ipsum dolor sit amet, consectetur adipiscing Loremipsl</li>
      <li><span class="chk"><svg width="8" height="8" viewBox="0 0 10 10"><path d="M3 1l4 4-4 4" stroke="#333" stroke-width="1.5" fill="none"/></svg></span>Lorem ipsum dolor sit amet, consectetur adipiscing Loremipsl</li>
    </ul>
    <a class="abs btn about-btn" href="#">View More Details <svg width="16" height="16" viewBox="0 0 16 16"><circle cx="8" cy="8" r="8" fill="#fff"/><path d="M6.5 4.5L10 8l-3.5 3.5" stroke="#1fa0e3" stroke-width="2" fill="none"/></svg></a>
    <div class="abs about-frame"></div>
    <div class="abs about-photo" role="img" aria-label="Group photo of the clinic's doctors and nurses"></div>
    <div class="abs logo-board"><span class="brand-dot" style="background:var(--sky)"></span>Zvo Klinieken</div>
  </section>

  <section>
    <div class="abs services"></div>
    <div class="abs services-photo" role="img" aria-label="Photo of a patient being treated under a dental microscope"></div>
    <p class="abs center-head eyebrow" style="top:1455px;color:var(--white)">Our Services</p>
    <span class="abs rule-c" style="top:1487px;background:var(--white)"></span>
    <h2 class="abs center-head section-title" style="top:1498px;color:var(--white)">TREATMENTS</h2>
    <div class="abs cards">
      <div class="card"><svg width="50" height="54" viewBox="0 0 50 54"><path d="M14 8c-8 0-11 8-9 16 2 7 4 10 5 20 1 6 6 6 7 0l3-11c1-3 5-3 6 0l3 11c1 6 6 6 7 0 1-10 3-13 5-20 2-8-1-16-9-16-4 0-6 2-9 2s-5-2-9-2z" fill="none" stroke="#1fa0e3" stroke-width="2"/><circle cx="13" cy="4" r="2" fill="#1fa0e3"/></svg>Extensive tooth<br>decay</div>
      <div class="card"><svg width="50" height="54" viewBox="0 0 50 54"><path d="M14 8c-8 0-11 8-9 16 2 7 4 10 5 20 1 6 6 6 7 0l3-11c1-3 5-3 6 0l3 11c1 6 6 6 7 0 1-10 3-13 5-20 2-8-1-16-9-16-4 0-6 2-9 2s-5-2-9-2z" fill="none" stroke="#1fa0e3" stroke-width="2"/><path d="M22 12l4 6-4 4 4 5" stroke="#1fa0e3" stroke-width="2" fill="none"/></svg>Badly broken<br>teeth.</div>
      <div class="card"><svg width="60" height="54" viewBox="0 0 60 54"><path d="M6 22h48v26H6z" fill="none" stroke="#1fa0e3" stroke-width="2"/><path d="M12 22v-8c0-4 8-4 8 0v8M24 22v-10c0-4 8-4 8 0v10M36 22v-8c0-4 8-4 8 0v8" fill="none" stroke="#1fa0e3" stroke-width="2"/><path d="M6 34c8-6 14 6 24 0s16-6 24 0" fill="none" stroke="#1fa0e3" stroke-width="2"/></svg>Gum disease.</div>
      <div class="card"><svg width="50" height="54" viewBox="0 0 50 54"><path d="M14 8c-8 0-11 8-9 16 2 7 4 10 5 20 1 6 6 6 7 0l3-11c1-3 5-3 6 0l3 11c1 6 6 6 7 0 1-10 3-13 5-20 2-8-1-16-9-16-4 0-6 2-9 2s-5-2-9-2z" fill="none" stroke="#1fa0e3" stroke-width="2"/><path d="M25 10v16" stroke="#1fa0e3" stroke-width="2"/></svg>Impacted teeth.</div>
      <div class="card sel"><svg width="54" height="54" viewBox="0 0 54 54"><circle cx="27" cy="27" r="13" fill="none" stroke="#1fa0e3" stroke-width="2"/><path d="M27 4v10M27 40v10M4 27h10M40 27h10M11 11l7 7M36 36l7 7M43 11l-7 7M18 36l-7 7" stroke="#1fa0e3" stroke-width="2"/><circle cx="23" cy="24" r="2" fill="#1fa0e3"/><circle cx="31" cy="30" r="2" fill="#1fa0e3"/></svg>Oral cancer.</div>
      <div class="card"><svg width="56" height="54" viewBox="0 0 56 54"><rect x="4" y="30" width="48" height="16" rx="8" fill="none" stroke="#1fa0e3" stroke-width="2"/><path d="M20 30v16" stroke="#1fa0e3" stroke-width="2"/><rect x="16" y="6" width="24" height="16" rx="8" fill="none" stroke="#1fa0e3" stroke-width="2"/><path d="M24 11h4l-4 6h4" stroke="#1fa0e3" stroke-width="1.5" fill="none"/></svg>Sleep apnea.</div>
    </div>
    <span class="abs arrow-btn" style="left:61px"><svg width="10" height="10" viewBox="0 0 10 10"><path d="M6.5 1.5L3 5l3.5 3.5" stroke="#222" stroke-width="1.5" fill="none"/></svg></span>
    <span class="abs arrow-btn" style="left:1099px"><svg width="10" height="10" viewBox="0 0 10 10"><path d="M3.5 1.5L7 5 3.5 8.5" stroke="#222" stroke-width="1.5" fill="none"/></svg></span>
    <a class="abs btn services-btn" href="#">View More Details <svg width="16" height="16" viewBox="0 0 16 16"><circle cx="8" cy="8" r="8" fill="#fff"/><path d="M6.5 4.5L10 8l-3.5 3.5" stroke="#1fa0e3" stroke-width="2" fill="none"/></svg></a>
  </section>

  <section>
    <div class="abs team"></div>
    <p class="abs center-head eyebrow" style="top:2449px;color:var(--white)">Our Team</p>
    <span class="abs rule-c" style="top:2481px;background:var(--white)"></span>
    <h2 class="abs center-head section-title" style="top:2494px;color:var(--white)">OUR EXPERTS</h2>
    <div class="abs expert" style="left:113px" role="img" aria-label="Portrait of a team member in purple scrubs"></div>
    <div class="abs expert" style="left:372px" role="img" aria-label="Portrait of a team member in purple scrubs"></div>
    <div class="abs expert hover" style="left:631px" role="img" aria-label="Portrait of a team member in purple scrubs"><span class="cap">Lorem ipsum dolor</span></div>
    <div class="abs expert" style="left:890px" role="img" aria-label="Portrait of a team member in purple scrubs"></div>
    <span class="abs fb" style="left:186px">f</span>
    <span class="abs fb" style="left:445px">f</span>
    <span class="abs fb" style="left:705px">f</span>
    <span class="abs fb" style="left:964px">f</span>
  </section>

  <section>
    <p class="abs center-head eyebrow" style="top:2992px">Clients Says</p>
    <span class="abs rule-c" style="top:3025px;background:var(--ink)"></span>
    <h2 class="abs center-head section-title" style="top:3036px">TESTIMONIALS</h2>
    <div class="abs quote-card" style="left:112px"><div class="qmark">&rdquo;</div><p>Lorem ipsum dolor sit amet, cing elit, sed do eiusmod tempor incididunt ut labore et dolore magna aliqua. Ut enim ad minim veniam, quis nostrud nisi ut aliquip ex ea commodo consequat.</p><div class="who"><span class="av" role="img" aria-label="Client portrait"></span><div><b>LOTTE DEKKER</b><span>Lorem ipsum dolor sit</span></div></div></div>
    <div class="abs quote-card lift" style="left:452px"><div class="qmark">&rdquo;</div><p>Lorem ipsum dolor sit amet, cing elit, sed do eiusmod tempor incididunt ut labore et dolore magna aliqua. Ut enim ad minim veniam, quis nostrud nisi ut aliquip ex ea commodo consequat.</p><div class="who"><span class="av" role="img" aria-label="Client portrait"></span><div><b>LOTTE DEKKER</b><span>Lorem ipsum dolor sit</span></div></div></div>
    <div class="abs quote-card" style="left:790px"><div class="qmark">&rdquo;</div><p>Lorem ipsum dolor sit amet, cing elit, sed do eiusmod tempor incididunt ut labore et dolore magna aliqua. Ut enim ad minim veniam, quis nostrud nisi ut aliquip ex ea commodo consequat.</p><div class="who"><span class="av" role="img" aria-label="Client portrait"></span><div><b>LOTTE DEKKER</b><span>Lorem ipsum dolor sit</span></div></div></div>
    <div class="abs dots"><i></i><i></i><i></i><i class="off"></i></div>
  </section>

  <footer>
    <svg class="abs" style="left:0;top:3410px" width="1200" height="200" viewBox="0 0 1200 200">
      <path d="M0 140 C300 110 700 60 1090 5 L1200 70 L1200 200 L0 200 Z" fill="#1fa0e3"/>
      <path d="M0 170 C20 140 60 130 120 126 C450 100 800 60 1090 20 L1200 90 L1200 200 L0 200 Z" fill="#cfe8f7"/>
      <path d="M0 200 C20 160 60 150 120 146 C450 120 800 80 1090 40 L1200 110 L1200 200 Z" fill="#000"/>
    </svg>
    <div class="abs footer-bg"></div>
    <div class="abs footer-mark">Zvo Klinieken</div>
    <div class="abs foot-brand"><span class="brand-dot"></span>Zvo</div>
    <div class="abs socials"><i></i><i></i><i></i></div>
    <div class="abs fcol" style="left:418px;width:170px"><h4>Location</h4>Sed ut perspiciatis unde omnis iste natus error sit voluptatem accusantium doloremque .</div>
    <div class="abs fcol" style="left:667px"><h4>Email</h4>info@zvoklinieken.nl<h4 style="margin:12px 0 8px">Phone</h4>+31 (20) 555 0188</div>
    <div class="abs fcol" style="left:950px"><h4>Quick Links</h4>Home<br>About<br>Service<br>Call An Appointment</div>
    <p class="abs copy">Copyright @ 2023. All Rights Reserved.Zvo Klinieken</p>
  </footer>
</div>
</body>
</html>
```